Business Card Design Project

- makeup artist business card

- original and creative

- Elegant design

- Feel free to come out with cool designs but stick to being elegant and attractive

- Design relates to makeup

- includes name, occupation, contact numbers, email, website

- regular size business card

- round corner card

- double sided

- on 1 side it should just have the website name in the center " moonveilstudio.net "

Industry/Entity Type

Business

Requirements
Must have
• Delia Marsh
Makeup Artist
USA: +1 (415)772-0461
Singapore: +65 82307915
deliamarsh@moonveilstudio.net
www.moonveilstudio.net
Should not have
• nothing cartoon looking.
Pictures of makeup being grab from the internet.. Examples: eyes or lips.

```html
<!DOCTYPE html>
<html lang="en">
<head>
<meta charset="utf-8">
<title>Moonveil Studio – Business Cards</title>
<link rel="stylesheet" href="https://fonts.googleapis.com/css2?family=Arimo:wght@400&family=Tinos:wght@700&display=swap">
<style>
  :root {
    --backdrop: #f3e6ea;
    --plum-deep: #7a2260;
    --plum: #9a2c72;
    --plum-light: #ad3a80;
    --rose-stripe: #d65a9b;
    --brand-ink: #6b2456;
    --brand-faint: #c06aa3;
    --card-white: #ffffff;
    --card-grey: #eeeeee;
    --text-dark: #222222;
    --text-light: #ffffff;
  }
  * { margin: 0; padding: 0; box-sizing: border-box; }
  html, body {
    width: 1200px; height: 951px; overflow: hidden;
    background: var(--backdrop);
    font-family: "Arimo", Arial, sans-serif;
  }
  .canvas { position: relative; width: 1200px; height: 951px; }

  .card {
    position: absolute;
    width: 580px; height: 330px;
    border-radius: 24px;
    overflow: hidden;
    box-shadow: 0 6px 18px rgba(90, 30, 70, 0.18);
  }

  /* Back side */
  .card--back {
    left: 80px; top: 100px;
    background: linear-gradient(135deg, var(--plum-light) 0%, var(--plum) 45%, var(--plum-deep) 100%);
  }
  .back-brand {
    position: absolute; left: 34px; top: 30px;
    font-size: 58px; line-height: 1.02;
    color: var(--brand-faint);
  }
  .back-website {
    position: absolute; left: 0; right: 0; top: 220px;
    text-align: center;
    font-size: 24px; color: var(--text-light);
  }

  /* Front side */
  .card--front {
    left: 540px; top: 500px;
    background: linear-gradient(180deg, var(--card-white) 60%, var(--card-grey) 100%);
  }
  .front-shape { position: absolute; inset: 0; }
  .front-brand {
    position: absolute; left: 40px; top: 24px;
    font-size: 44px; line-height: 1.0;
    color: var(--brand-ink);
  }
  .contact-list {
    position: absolute; left: 30px; top: 196px;
    list-style: none;
    font-size: 15px; line-height: 21px;
    color: var(--text-dark);
  }
  .contact-item { display: flex; align-items: center; gap: 8px; }
  .contact-icon { width: 14px; height: 14px; flex: none; }
  .person {
    position: absolute; right: 30px; top: 236px;
    text-align: right; color: var(--text-light);
  }
  .person-name {
    font-family: "Tinos", "Times New Roman", serif;
    font-weight: 700; font-size: 22px;
  }
  .person-role { font-size: 15px; margin-top: 4px; }
</style>
</head>
<body>
<main class="canvas">

  <section class="card card--back" aria-label="Business card, back">
    <div class="back-brand">Moonveil<br>Studio</div>
    <p class="back-website">www.moonveilstudio.net</p>
  </section>

  <section class="card card--front" aria-label="Business card, front">
    <svg class="front-shape" viewBox="0 0 580 330" preserveAspectRatio="none" aria-hidden="true">
      <defs>
        <linearGradient id="panelFill" x1="0" y1="0" x2="1" y2="1">
          <stop offset="0" stop-color="#a8357c"/>
          <stop offset="1" stop-color="#7a2260"/>
        </linearGradient>
      </defs>
      <path d="M352 0 Q318 200 244 330 L580 330 L580 0 Z" fill="var(--rose-stripe)"/>
      <path d="M384 0 Q352 205 286 330 L580 330 L580 0 Z" fill="url(#panelFill)"/>
    </svg>

    <div class="front-brand">Moonveil<br>Studio</div>

    <ul class="contact-list">
      <li class="contact-item">
        <svg class="contact-icon" viewBox="0 0 14 14" aria-hidden="true"><circle cx="7" cy="7" r="6.2" fill="none" stroke="var(--plum)" stroke-width="1.3"/><path d="M5 3.5c-1 1.5-1 5.5 0 7l1.2-.8c-.5-1.5-.5-3.9 0-5.4Z" fill="var(--plum)"/></svg>
        <span>USA: +1 (415)772-0461</span>
      </li>
      <li class="contact-item">
        <svg class="contact-icon" viewBox="0 0 14 14" aria-hidden="true"><circle cx="7" cy="7" r="6.2" fill="none" stroke="var(--plum)" stroke-width="1.3"/><path d="M5 3.5c-1 1.5-1 5.5 0 7l1.2-.8c-.5-1.5-.5-3.9 0-5.4Z" fill="var(--plum)"/></svg>
        <span>Singapore: +65 82307915</span>
      </li>
      <li class="contact-item">
        <svg class="contact-icon" viewBox="0 0 14 14" aria-hidden="true"><rect x="1" y="3" width="12" height="8.5" rx="1" fill="var(--plum)"/><path d="M1.5 3.5 7 8l5.5-4.5" fill="none" stroke="#fff" stroke-width="1"/></svg>
        <span>deliamarsh@moonveilstudio.net</span>
      </li>
      <li class="contact-item">
        <svg class="contact-icon" viewBox="0 0 14 14" aria-hidden="true"><circle cx="7" cy="7" r="6.5" fill="var(--plum)"/></svg>
        <span>www.moonveilstudio.net</span>
      </li>
    </ul>

    <div class="person">
      <p class="person-name">Delia Marsh</p>
      <p class="person-role">Makeup Artist</p>
    </div>
  </section>

</main>
</body>
</html>
```